Business Card Design For A Cajun Seafood Restaurant

We are opening a cajun seafood restaurant in a week. We mainly serve cajun seafood which is orginally from Louisiana. We want design on both sides of a business card. I have menu on the website. You can go to www.reednkettle.example to check out our menu.

Restaurant name: Reed N' Kettle
Phone: +1 (555) 304-7712
Address: 48206 Ludlow Row, #7, Bexmoor Flats, Ca90000
Email: reednkettle@mailbox.example
Website: www.reednkettle.example

Maybe add social media icons (facebook, instagram) if looks nice on the business card.
facebook.com/reednkettle
instagram.com/reednkettle or @reednkettle

Attached is the logo and other business card samples that I like.

```html
<!DOCTYPE html>
<html lang="en">
<head>
<meta charset="utf-8">
<title>Reed N' Kettle — Business Card</title>
<link rel="stylesheet" href="https://fonts.googleapis.com/css2?family=Open+Sans:wght@400;700&display=swap">
<style>
  :root {
    --page: #d6d8da;
    --card-black: #120d0a;
    --card-yellow: #e2b500;
    --ink: #1a1408;
    --name-front: #f07a1a;
    --art-warm: #e8591c;
    --art-light: #f2c21b;
    --line: #3a2d05;
  }
  * { box-sizing: border-box; margin: 0; padding: 0; }
  html, body { width: 1200px; height: 864px; overflow: hidden; }
  body {
    background: var(--page);
    font-family: "Open Sans", Arial, sans-serif;
    position: relative;
  }
  .card {
    position: absolute;
    left: 270px;
    width: 660px;
    height: 377px;
    border-radius: 3px;
    overflow: hidden;
    box-shadow: 0 6px 18px rgba(0,0,0,.18);
  }
  .card--front { top: 32px; background: var(--card-black); }
  .card--back { top: 455px; background: var(--card-yellow); color: var(--ink); }

  .background-art {
    position: absolute;
    border-radius: 50%;
  }
  .card--front .background-art {
    left: 40px; top: 40px; width: 300px; height: 300px;
    background: radial-gradient(circle, rgba(60,40,20,.35), rgba(18,13,10,0) 70%);
  }
  .card--back .background-art {
    left: -40px; top: 40px; width: 330px; height: 330px;
    background: radial-gradient(circle, rgba(255,215,60,.45), rgba(226,181,0,0) 70%);
  }

  .mascot-art {
    position: absolute;
    border-radius: 50%;
    background: radial-gradient(circle, var(--art-light) 0 20%, var(--art-warm) 60%, rgba(232,89,28,0) 72%);
  }
  .card--front .mascot-art { left: 265px; top: 70px; width: 130px; height: 120px; }
  .card--back .mascot-art { left: 365px; top: 30px; width: 150px; height: 140px; }

  .brand-name {
    position: absolute;
    font-weight: 700;
    white-space: nowrap;
    text-align: center;
  }
  .card--front .brand-name {
    left: 0; right: 0; top: 200px;
    font-size: 26px;
    color: var(--name-front);
  }
  .card--back .brand-name {
    left: 280px; width: 350px; top: 163px;
    font-size: 28px;
    color: var(--ink);
  }

  .social {
    position: absolute;
    left: 32px; top: 24px;
    list-style: none;
    font-size: 17px;
  }
  .social li { display: flex; align-items: center; gap: 8px; height: 28px; }
  .social__mark {
    width: 14px; height: 14px; background: var(--ink); border-radius: 2px;
  }

  .divider {
    position: absolute;
    left: 0; right: 0; top: 212px;
    border-top: 1.5px solid var(--line);
  }

  .address {
    position: absolute;
    left: 32px; top: 240px;
    font-size: 15px;
    line-height: 22px;
    font-style: normal;
  }

  .contacts {
    position: absolute;
    left: 380px; top: 262px;
    list-style: none;
    font-size: 15.5px;
  }
  .contacts li { display: flex; align-items: center; gap: 8px; height: 22px; }
  .contacts svg { width: 12px; height: 12px; fill: var(--ink); flex: none; }
</style>
</head>
<body>

  <section class="card card--front" aria-label="Card front">
    <div class="background-art" role="img" aria-label="Faint mascot illustration in the background"></div>
    <div class="mascot-art" role="img" aria-label="Mascot illustration above the restaurant name"></div>
    <p class="brand-name">Reed N' Kettle</p>
  </section>

  <section class="card card--back" aria-label="Card back">
    <div class="background-art" role="img" aria-label="Faint mascot illustration in the background"></div>

    <ul class="social">
      <li><span class="social__mark"></span>/reednkettle</li>
      <li><span class="social__mark"></span>/reednkettle</li>
    </ul>

    <div class="mascot-art" role="img" aria-label="Mascot illustration above the restaurant name"></div>
    <p class="brand-name">Reed N' Kettle</p>

    <div class="divider"></div>

    <address class="address">48206 Ludlow Row,<br>#7, Bexmoor Flats, Ca90000</address>

    <ul class="contacts">
      <li>
        <svg viewBox="0 0 24 24"><path d="M6.6 10.8a15.1 15.1 0 0 0 6.6 6.6l2.2-2.2a1 1 0 0 1 1-.25 11.4 11.4 0 0 0 3.6.57 1 1 0 0 1 1 1V20a1 1 0 0 1-1 1A17 17 0 0 1 3 4a1 1 0 0 1 1-1h3.5a1 1 0 0 1 1 1c0 1.25.2 2.45.57 3.57a1 1 0 0 1-.25 1z"/></svg>
        +1 (555) 304-7712
      </li>
      <li>
        <svg viewBox="0 0 24 24"><path d="M2 5h20v14H2z"/><path d="M3 6l9 7 9-7" fill="none" stroke="#e2b500" stroke-width="1.8"/></svg>
        reednkettle@mailbox.example
      </li>
      <li>
        <svg viewBox="0 0 24 24"><circle cx="12" cy="12" r="10"/></svg>
        www.reednkettle.example
      </li>
    </ul>
  </section>

</body>
</html>
```